Need business card with a logo for a hearing aid sales and audiology business. We have two Hearing Instrument Specialists and one Audiologist on staff. Over 25 years in business. Locally owned and operated. Financing available. Most insurances accepted.

Summit Audio Wellness LLC
48730 W Larchmont, Suite 7
Spokane, WA 99281
509-617-2084
www.summitaudiowell.example

Manager
Tobias Kerrell HIS COHC
License #71829046

Target Market(s)

50yr old + people with a hearing loss.

Industry/Entity Type

Business

Contact Information for Business Card

48730 W Larchmont, Suite 7
Spokane, WA 99281
509-617-2084
www.summitaudiowell.example

Manager
Tobias Kerrell HIS COHC
NLVE #71829046

Font styles to use
Serif
Sans Serif

Requirements
Must have
• Business name, Tobias's name and title(s) and contact information, License #, web address

```html
<!DOCTYPE html>
<html lang="en">
<head>
<meta charset="utf-8">
<title>Summit Audio Wellness – Business Card</title>
<link rel="stylesheet" href="https://fonts.googleapis.com/css2?family=Marcellus+SC&display=swap">
<style>
  :root {
    --backdrop: #1e1e1e;
    --card: #f7f7f5;
    --green: #8cc63f;
    --green-deep: #7ab32e;
    --ink: #3a3a3a;
  }
  * { margin: 0; padding: 0; box-sizing: border-box; }
  html, body {
    width: 1200px; height: 800px; overflow: hidden;
    background: var(--backdrop);
    font-family: "Marcellus SC", "Times New Roman", serif;
  }
  .card {
    position: absolute; left: 100px; top: 114px;
    width: 1000px; height: 572px;
    background: var(--card);
    border-radius: 34px;
    overflow: hidden;
  }
  .card__band {
    position: absolute; left: 0; right: 0; bottom: 0; height: 78px;
    background: linear-gradient(to bottom, var(--card) 0%, #dcebc4 35%, var(--green) 100%);
  }
  .brand { position: absolute; left: 120px; top: 70px; }
  .brand__dot {
    width: 110px; height: 110px; border-radius: 50%;
    background: var(--green); margin: 0 0 22px 60px;
  }
  .brand__name {
    font-size: 34px; letter-spacing: 2px; color: var(--ink); white-space: nowrap;
  }
  .rule { position: absolute; height: 1.5px; background: var(--green); }
  .rule--main { left: 100px; right: 70px; top: 316px; }
  .rule--address { left: 520px; right: 70px; top: 470px; }
  .rule--web { left: 60px; width: 290px; top: 497px; }
  .contact { position: absolute; left: 100px; top: 330px; font-size: 28px; color: var(--ink); line-height: 44px; }
  .contact__value { color: var(--green); }
  .person { position: absolute; right: 70px; top: 262px; text-align: right; color: var(--ink); }
  .person__name { font-size: 38px; color: var(--green); }
  .person__creds { font-size: 30px; margin-left: 8px; }
  .person__role { font-size: 28px; margin-top: 6px; line-height: 34px; }
  .address { position: absolute; right: 70px; top: 382px; text-align: right; color: var(--green); font-size: 30px; line-height: 38px; }
  .web {
    position: absolute; left: 370px; top: 478px;
    display: flex; align-items: center; gap: 12px;
    font-size: 34px; color: #222; letter-spacing: 0.5px;
  }
  .web svg { width: 30px; height: 30px; }
</style>
</head>
<body>
  <div class="card">
    <div class="card__band"></div>

    <div class="brand">
      <div class="brand__dot"></div>
      <div class="brand__name">Summit Audio Wellness</div>
    </div>

    <div class="rule rule--main"></div>

    <div class="contact">
      <div>Ph: <span class="contact__value">509-617-2084</span></div>
      <div>NLVE: <span class="contact__value">#71829046</span></div>
    </div>

    <div class="person">
      <div><span class="person__name">Tobias Kerrell</span><span class="person__creds">HIS COHC</span></div>
      <div class="person__role">Manager</div>
    </div>

    <div class="address">
      <div>48730 W Larchmont, Suite 7</div>
      <div>Spokane, WA 99281</div>
    </div>
    <div class="rule rule--address"></div>

    <div class="rule rule--web"></div>
    <div class="web">
      <svg viewBox="0 0 30 30" aria-hidden="true">
        <circle cx="15" cy="15" r="13" fill="none" stroke="#222" stroke-width="2.2"/>
        <ellipse cx="15" cy="15" rx="5.5" ry="13" fill="none" stroke="#222" stroke-width="1.8"/>
        <line x1="2" y1="15" x2="28" y2="15" stroke="#222" stroke-width="1.8"/>
        <line x1="5" y1="8.5" x2="25" y2="8.5" stroke="#222" stroke-width="1.5"/>
        <line x1="5" y1="21.5" x2="25" y2="21.5" stroke="#222" stroke-width="1.5"/>
      </svg>
      <span>www.summitaudiowell.example</span>
    </div>
  </div>
</body>
</html>
```